4th Generation Family Business Needs a New Card Design!

We are a family owned 4th Generation company. We are based in the Sydney, Australia area and we are desperately in need of a more modern and classy card. We are monumental masons who design, supply & erect lasting memorials throughout cemeteries in Sydney. Our customers are normally in a period of grieving. I have attached logo files that will need to be implemented on the card. Company was established 1935. Australian Owned and Operated. Card needs to be designed to PIXO.com specification.

Target Market(s)

Our target market is based upon people that a grieving for family members that have passed away. We also deal with alot of companies that own and operate cemeteries.

Industry/Entity Type

Business

Contact Information for Business Card

Simon Harcourt, Operations Manager, 0417293086, simon@harcourtmemorials.com.au
Lewis Harcourt, Director, 0491630572, lewis@harcourtmemorials.com.au
Phone # 02 9561 3048
Website: www.harcourtmemorials.com.au
Address: Suite 17, 8 Palfrey Lane, West Carlow, Sydney NSW 2156

Font styles to use
Serif
Decorative
Script

Requirements
Must have
• Would like to see the logo nicely implemented with a modern design. Embossed lettering would be a nice additive.

```html
<!DOCTYPE html>
<html lang="en">
<head>
<meta charset="utf-8">
<title>Harcourt Memorials – Business Card</title>
<link href="https://fonts.googleapis.com/css2?family=Cinzel:wght@400;600&family=Open+Sans:wght@400&display=swap" rel="stylesheet">
<style>
  :root {
    --backdrop: #4a413b;
    --card: #1b1b1b;
    --card-edge: #262626;
    --gold: #e6b422;
    --text: #e9e9e9;
    --muted: #bdbdbd;
    --divider: #3a3a3a;
    --emboss: #3b3b3b;
  }
  * { margin: 0; padding: 0; box-sizing: border-box; }
  html, body { width: 1200px; height: 716px; overflow: hidden; }
  body {
    background: var(--backdrop);
    display: flex;
    align-items: center;
    justify-content: center;
    gap: 60px;
    font-family: "Open Sans", Arial, sans-serif;
  }
  .card {
    width: 500px;
    height: 286px;
    background: var(--card);
    border: 1px solid var(--card-edge);
    box-shadow: 0 12px 30px rgba(0,0,0,0.45);
    position: relative;
  }
  /* Front */
  .card-front { display: flex; }
  .brand-panel {
    width: 240px;
    display: flex;
    flex-direction: column;
    align-items: center;
    justify-content: center;
    gap: 14px;
  }
  .brand-square {
    width: 34px; height: 34px;
    background: var(--gold);
  }
  .brand-name {
    font-family: "Cinzel", Georgia, serif;
    font-weight: 600;
    font-size: 21px;
    letter-spacing: 2px;
    color: var(--text);
    text-align: center;
    line-height: 1.3;
  }
  .divider {
    width: 1px;
    margin: 40px 0;
    background: var(--divider);
  }
  .contact-panel {
    flex: 1;
    padding: 48px 22px 0 24px;
    color: var(--text);
    font-size: 11.5px;
    line-height: 1.45;
  }
  .person-name {
    font-family: "Cinzel", Georgia, serif;
    font-size: 16px;
    color: var(--gold);
    letter-spacing: 1px;
    line-height: 1.2;
  }
  .person-role { color: var(--muted); margin-bottom: 14px; }
  .address { margin-bottom: 10px; }
  .contact-list { list-style: none; }
  .contact-list li { display: flex; align-items: center; gap: 6px; }
  .contact-list svg { width: 10px; height: 10px; flex: none; fill: var(--gold); }
  /* Back */
  .card-back {
    display: flex;
    flex-direction: column;
    align-items: center;
    justify-content: center;
    gap: 16px;
  }
  .card-back .brand-square { width: 44px; height: 44px; background: var(--emboss); }
  .card-back .brand-name {
    font-size: 30px;
    font-weight: 400;
    color: var(--emboss);
    letter-spacing: 3px;
  }
</style>
</head>
<body>
  <section class="card card-front">
    <div class="brand-panel">
      <div class="brand-square"></div>
      <div class="brand-name">Harcourt<br>Memorials</div>
    </div>
    <div class="divider"></div>
    <div class="contact-panel">
      <h1 class="person-name">Simon Harcourt</h1>
      <p class="person-role">Operations Manager</p>
      <p class="address">Suite 17, 8 Palfrey Lane, West Carlow,<br>Sydney NSW 2156</p>
      <ul class="contact-list">
        <li><svg viewBox="0 0 10 10"><rect x="2.5" y="0" width="5" height="10" rx="1"/></svg>0417293086</li>
        <li><svg viewBox="0 0 10 10"><path d="M2 0h2l1 3-1.5 1a6 6 0 0 0 2.5 2.5L7 5l3 1v2c0 1-1 2-2 2A8 8 0 0 1 0 2c0-1 1-2 2-2z"/></svg>02 9561 3048</li>
        <li><svg viewBox="0 0 10 10"><path d="M0 2h10v6H0z M0 2l5 3.5L10 2" stroke="#1b1b1b" stroke-width="0.8"/></svg>simon@harcourtmemorials.com.au</li>
        <li><svg viewBox="0 0 10 10"><circle cx="5" cy="5" r="5"/></svg>www.harcourtmemorials.com.au</li>
      </ul>
    </div>
  </section>

  <section class="card card-back">
    <div class="brand-square"></div>
    <div class="brand-name">Harcourt Memorials</div>
  </section>
</body>
</html>
```